Business Card for a Dental Office

The design should communicate integrity, quality and reliability. We also want the card look elegant, simple, but still stand out, different from the traditional-dental-office business card.

Industry/Entity Type

Business

```html
<!DOCTYPE html>
<html lang="en">
<head>
<meta charset="utf-8">
<title>Harlow Dental Centre – Business Card</title>
<link rel="stylesheet" href="https://fonts.googleapis.com/css2?family=Oswald:wght@500&family=Open+Sans:wght@400;600&display=swap">
<style>
  :root {
    --page-bg: #4a4a4a;
    --card-white: #ffffff;
    --card-black: #000000;
    --ink: #111111;
    --ink-soft: #444444;
    --gold: #b08d1e;
    --gold-bright: #e8dc10;
    --gold-deep: #c9a51a;
    --rule: #555555;
  }
  * { box-sizing: border-box; margin: 0; padding: 0; }
  html, body { width: 1105px; height: 1200px; overflow: hidden; }
  body { background: var(--page-bg); font-family: "Open Sans", Arial, sans-serif; position: relative; }

  .card { position: absolute; left: 196px; width: 720px; height: 411px; }
  .card-front { top: 146px; background: var(--card-white); }
  .card-back { top: 602px; background: var(--card-black); overflow: hidden; }

  /* Front */
  .brand-square { position: absolute; left: 143px; top: 72px; width: 100px; height: 100px; background: var(--ink); }
  .front-brand { position: absolute; left: 260px; top: 112px; }
  .brand-name { font-family: "Oswald", "Arial Narrow", sans-serif; font-weight: 500; font-size: 33px; line-height: 1; color: var(--ink); letter-spacing: 0.2px; white-space: nowrap; }
  .brand-tagline { font-family: "Open Sans", Arial, sans-serif; font-weight: 600; font-size: 12px; color: var(--gold); letter-spacing: 0.9px; margin-top: 5px; white-space: nowrap; }

  .front-rule { position: absolute; left: 32px; right: 32px; top: 263px; height: 2px; background: var(--rule); }

  .person { position: absolute; left: 32px; top: 282px; }
  .person-name { font-size: 26px; font-weight: 600; color: var(--ink); line-height: 1.2; }
  .person-role { font-size: 19px; color: var(--gold); line-height: 1.35; }
  .person-address { font-size: 18.5px; color: var(--ink-soft); line-height: 1.45; }

  .contact-list { position: absolute; right: 28px; top: 288px; list-style: none; }
  .contact-item { display: flex; justify-content: flex-end; align-items: center; gap: 12px; font-size: 18.5px; color: var(--ink-soft); line-height: 27.5px; }
  .contact-icon { width: 18px; height: 18px; fill: var(--ink); flex: none; }

  /* Back */
  .back-mark { position: absolute; left: 40px; top: 40px; width: 330px; height: 330px;
    background: radial-gradient(circle at 55% 45%, var(--gold-bright), var(--gold-deep) 75%); }
  .back-lockup { position: absolute; left: 407px; top: 300px; }
  .back-lockup .brand-name { color: var(--gold-bright); font-size: 28px; }
  .back-lockup .brand-tagline { color: var(--gold-deep); font-size: 10.5px; letter-spacing: 0.6px; margin-top: 3px; }
  .back-web { font-size: 17px; color: var(--gold-deep); letter-spacing: 4px; margin-top: 4px; white-space: nowrap; }
</style>
</head>
<body>
  <section class="card card-front">
    <div class="brand-square"></div>
    <div class="front-brand">
      <p class="brand-name">HARLOW DENTAL CENTRE</p>
      <p class="brand-tagline">GENTLE CARE FOR EVERY FAMILY SMILE</p>
    </div>
    <div class="front-rule"></div>
    <div class="person">
      <p class="person-name">Daniel Reyes</p>
      <p class="person-role">CEO/Founder</p>
      <p class="person-address">1240 Willowbank Road<br>Fairview, Oregon 97024</p>
    </div>
    <ul class="contact-list">
      <li class="contact-item">555 210 4817
        <svg class="contact-icon" viewBox="0 0 24 24"><path d="M6.6 10.8a15 15 0 0 0 6.6 6.6l2.2-2.2c.3-.3.7-.4 1-.2 1.1.4 2.3.6 3.6.6.6 0 1 .4 1 1V20c0 .6-.4 1-1 1C10.6 21 3 13.4 3 4c0-.6.4-1 1-1h3.5c.6 0 1 .4 1 1 0 1.3.2 2.5.6 3.6.1.3 0 .7-.2 1z"/></svg>
      </li>
      <li class="contact-item">555 392 0651
        <svg class="contact-icon" viewBox="0 0 24 24"><path d="M7 1h10a2 2 0 0 1 2 2v18a2 2 0 0 1-2 2H7a2 2 0 0 1-2-2V3a2 2 0 0 1 2-2zm0 3v14h10V4zm5 15.2a1.2 1.2 0 1 0 0 2.4 1.2 1.2 0 0 0 0-2.4z"/></svg>
      </li>
      <li class="contact-item">hello@harlowdental.com
        <svg class="contact-icon" viewBox="0 0 24 24"><path d="M2 5h20v14H2zm2 2v.5l8 5 8-5V7l-8 5z"/></svg>
      </li>
      <li class="contact-item">www.harlowdental.com
        <svg class="contact-icon" viewBox="0 0 24 24"><circle cx="12" cy="12" r="10"/><path d="M7 8c2 0 3 1 3 3s-2 2-2 4l-2 2M15 5c-1 2 0 3 2 3s2 2 1 4-3 2-3 5" stroke="#fff" stroke-width="1.6" fill="none"/></svg>
      </li>
    </ul>
  </section>

  <section class="card card-back">
    <div class="back-mark" role="img" aria-label="Brand emblem area"></div>
    <div class="back-lockup">
      <p class="brand-name">HARLOW DENTAL CENTRE</p>
      <p class="brand-tagline">GENTLE CARE FOR EVERY FAMILY SMILE</p>
      <p class="back-web">www.harlowdental.com</p>
    </div>
  </section>
</body>
</html>
```